Business Card for a mobile physiotherapy company

I need a layout for a business card for a mobile physiotherapy company.
Slogan is "Mobile Physiotherapy - Your Road To Recovery"
Phone number is 867-555-0142
Email VardenTherapy@postnest.ca (subject to change with website)
Website www.VardenTherapy.ca
My name and credentials: Luke Varden Luke Varden, BSc(kin), MPT, CAFCI, IMS
Information maybe included: Direct Billing, Services including Physiotherapy, IMS, acupuncture
Maybe include facebook and instagram logos
One side with the logo clean and sharp
Other side with details, try not to look too busy, keep everything concise

```html
<!DOCTYPE html>
<html lang="en">
<head>
<meta charset="utf-8">
<title>Varden Therapy – Business Card</title>
<link href="https://fonts.googleapis.com/css2?family=Noto+Serif:wght@700&family=Source+Sans+3:wght@400;600&display=swap" rel="stylesheet">
<style>
  :root {
    --navy: #2c4a72;
    --green: #0f5a48;
    --ink: #1d1d1f;
    --white: #ffffff;
    --rule: #bdbdbd;
    --bg-light: #e7e8e9;
    --bg-dark: #b3b4b7;
  }
  * { box-sizing: border-box; margin: 0; padding: 0; }
  html, body { width: 1200px; height: 1113px; overflow: hidden; }
  body {
    position: relative;
    background: linear-gradient(90deg, var(--bg-light), var(--bg-dark));
    font-family: "Source Sans 3", sans-serif;
  }
  .card {
    position: absolute;
    width: 768px;
    height: 438px;
    border-radius: 42px;
    overflow: hidden;
  }
  .card-front { left: 349px; top: 81px; background: var(--white); }
  .card-back { left: 88px; top: 574px; background: var(--navy); }

  .brand-name {
    position: absolute;
    text-align: center;
    font-family: "Source Sans 3", sans-serif;
    font-weight: 600;
    font-size: 40px;
    line-height: 1.15;
  }
  .card-front .brand-name { left: 44px; width: 342px; top: 130px; color: var(--navy); }
  .card-back .brand-name { left: 0; width: 768px; top: 150px; color: var(--white); font-size: 46px; }

  .divider {
    position: absolute; left: 399px; top: 53px;
    width: 2px; height: 257px; background: var(--rule);
  }
  .details { position: absolute; left: 432px; top: 50px; color: var(--ink); }
  .person-name {
    font-family: "Noto Serif", serif; font-weight: 700;
    font-size: 26px; color: var(--navy); letter-spacing: 0.5px; line-height: 1.1;
  }
  .credentials { font-size: 15px; margin-top: 6px; }
  .contact-list { list-style: none; margin-top: 14px; }
  .contact-item {
    display: flex; align-items: center; gap: 7px;
    font-size: 19.5px; height: 32.5px;
  }
  .contact-icon { width: 19px; height: 19px; flex: none; }
  .services-title {
    font-weight: 600; font-size: 19px; color: var(--navy); margin-top: 14px;
  }
  .services-list {
    list-style: none; display: grid;
    grid-template-columns: 152px auto; row-gap: 4px;
    margin-top: 9px; font-size: 19px; color: var(--green);
  }
  .services-list li::before { content: "• "; font-size: 14px; vertical-align: 2px; }

  .footer-rule {
    position: absolute; left: 0; top: 358px;
    width: 768px; height: 4px; background: var(--green);
  }
  .footer-band {
    position: absolute; left: 0; top: 368px;
    width: 768px; height: 70px; background: var(--navy);
  }
  .slogan {
    position: absolute; left: 40px; width: 330px; top: 374px;
    text-align: center; color: var(--white);
    font-family: "Noto Serif", serif; font-weight: 700;
    font-size: 18.5px; line-height: 29px;
  }

  .socials {
    position: absolute; top: 348px; left: 167px;
    display: flex; align-items: center; color: var(--white); font-size: 24px;
  }
  .social-item { display: flex; align-items: center; gap: 12px; }
  .social-item + .social-item { margin-left: 26px; }
  .social-square { width: 48px; height: 48px; border-radius: 6px; background: var(--white); }
</style>
</head>
<body>

<section class="card card-front">
  <p class="brand-name">Varden<br>Therapy</p>

  <div class="divider"></div>

  <div class="details">
    <h1 class="person-name">LUKE VARDEN</h1>
    <p class="credentials">BSc(kin), MPT, CAFCI, IMS</p>
    <ul class="contact-list">
      <li class="contact-item">
        <svg class="contact-icon" viewBox="0 0 20 20" fill="none" stroke="#2c4a72" stroke-width="1.6">
          <circle cx="10" cy="10" r="8.6"/>
          <path d="M6.5 5.5c-.6.6-.9 1.6 0 3.4 1 2 2.7 3.7 4.6 4.6 1.8.9 2.8.6 3.4 0l.4-.9-2-1.6-1.2.8c-1-.4-2.3-1.7-2.8-2.8l.8-1.2-1.6-2z" fill="#2c4a72" stroke="none"/>
        </svg>
        867-555-0142
      </li>
      <li class="contact-item">
        <svg class="contact-icon" viewBox="0 0 20 20" fill="none" stroke="#2c4a72" stroke-width="1.6">
          <circle cx="10" cy="10" r="8.6"/>
          <rect x="5.5" y="7" width="9" height="6.5" rx="1"/>
          <path d="M5.8 7.4 10 10.6l4.2-3.2"/>
        </svg>
        VardenTherapy@postnest.ca
      </li>
      <li class="contact-item">
        <svg class="contact-icon" viewBox="0 0 20 20" fill="none" stroke="#2c4a72" stroke-width="1.3">
          <circle cx="10" cy="10" r="8.6"/>
          <ellipse cx="10" cy="10" rx="3.6" ry="8.6"/>
          <path d="M1.4 10h17.2M2.8 6h14.4M2.8 14h14.4M10 1.4v17.2"/>
        </svg>
        www.VardenTherapy.ca
      </li>
    </ul>
    <h2 class="services-title">Services Including</h2>
    <ul class="services-list">
      <li>Physiotherapy</li>
      <li>Direct Billing</li>
      <li>Ims</li>
      <li>Acupuncture</li>
    </ul>
  </div>

  <div class="footer-rule"></div>
  <div class="footer-band"></div>
  <p class="slogan">Mobile Physiotherapy -<br>Your Road To Recovery</p>
</section>

<section class="card card-back">
  <p class="brand-name">Varden<br>Therapy</p>

  <div class="socials">
    <div class="social-item">
      <span class="social-square"></span>
      <span>VardenTherapy</span>
    </div>
    <div class="social-item">
      <span class="social-square"></span>
      <span>@VardenTherapy</span>
    </div>
  </div>
</section>

</body>
</html>
```